Business Card Design For A Cajun Seafood Restaurant

We are opening a cajun seafood restaurant in a week. We mainly serve cajun seafood which is orginally from Louisiana. We want design on both sides of a business card. I have menu on the website. You can go to www.reednkettle.example to check out our menu.

Restaurant name: The Reed Kettle
Phone: +1 (555) 304-7712
Address: 48206 Ludlow Row, #7, Bexmoor Flats, Ca90000
Email: reednkettle@mailbox.example
Website: www.reednkettle.example

Maybe add social media icons (facebook, instagram) if looks nice on the business card.
facebook.com/reednkettle
instagram.com/reednkettle or @reednkettle

Attached is the logo and other business card samples that I like.

```html
<!DOCTYPE html>
<html lang="en">
<head>
<meta charset="utf-8">
<title>The Reed Kettle — Business Card</title>
<link href="https://fonts.googleapis.com/css2?family=Roboto:wght@400;500;700&display=swap" rel="stylesheet">
<style>
  :root {
    --backdrop: #e6e6e6;
    --kraft: #c8a779;
    --kraft-deep: #b8956a;
    --ink: #1f1b17;
    --ink-soft: #2e2923;
    --rule: #4a4038;
    --crab-orange: #cf5f2c;
    --corn-yellow: #e2b427;
    --band-orange: #d6612a;
    --band-yellow: #e1b526;
    --white: #ffffff;
  }
  * { margin: 0; padding: 0; box-sizing: border-box; }
  html, body {
    width: 1200px; height: 576px; overflow: hidden;
    background: var(--backdrop);
    font-family: "Roboto", Arial, sans-serif;
    color: var(--ink);
  }
  .canvas { position: relative; width: 1200px; height: 576px; }

  .card {
    position: absolute; top: 139px;
    width: 484px; height: 293px;
    border-radius: 7px; overflow: hidden;
    background: radial-gradient(circle at 40% 35%, var(--kraft) 0%, var(--kraft) 60%, var(--kraft-deep) 100%);
  }
  .card--front { left: 82px; }
  .card--back { left: 602px; }

  .mascot {
    position: absolute;
    background: radial-gradient(ellipse at 50% 55%, var(--crab-orange) 0%, #d9783f 45%, rgba(226,180,39,0.55) 75%, rgba(200,167,121,0) 100%);
    border-radius: 40%;
  }
  .card--front .mascot { left: 182px; top: 55px; width: 136px; height: 118px; }
  .card--back .mascot { left: 24px; top: 19px; width: 134px; height: 128px; }

  .brand {
    position: absolute;
    display: flex; align-items: center; gap: 8px;
    font-weight: 700; color: var(--ink);
    white-space: nowrap;
  }
  .brand__mark { width: 12px; height: 12px; background: var(--crab-orange); }
  .card--front .brand { left: 0; right: 0; justify-content: center; top: 182px; font-size: 30px; }
  .card--back .brand { right: 28px; top: 40px; font-size: 24px; }

  .person { position: absolute; right: 28px; top: 140px; text-align: right; }
  .person__name { font-size: 19px; font-weight: 500; color: var(--ink-soft); line-height: 22px; }
  .person__role { font-size: 11px; color: var(--ink-soft); line-height: 14px; }

  .divider { position: absolute; left: 24px; top: 175px; width: 326px; height: 1px; background: var(--rule); }

  .contacts { position: absolute; left: 28px; top: 193px; list-style: none; }
  .contacts li {
    display: flex; align-items: center; gap: 8px;
    height: 17.8px; font-size: 12.5px; color: var(--ink-soft);
  }
  .contacts svg { width: 10px; height: 10px; flex: none; }
  .contacts .social-box { width: 9px; height: 9px; background: var(--ink-soft); border-radius: 1.5px; flex: none; margin: 0 0.5px; }

  .address {
    position: absolute; right: 28px; top: 204px;
    text-align: right; font-size: 12.5px; line-height: 18px; color: var(--ink-soft);
  }

  .bands { position: absolute; left: 0; bottom: 0; width: 484px; height: 38px; }
  .website {
    position: absolute; right: 28px; bottom: 11px;
    font-size: 12px; color: var(--white);
  }
</style>
</head>
<body>
<main class="canvas">

  <section class="card card--front" aria-label="Business card front">
    <div class="mascot" role="img" aria-label="Illustrated crab mascot holding an ear of corn"></div>
    <div class="brand"><span class="brand__mark"></span>The Reed Kettle</div>
  </section>

  <section class="card card--back" aria-label="Business card back">
    <div class="mascot" role="img" aria-label="Illustrated crab mascot holding an ear of corn"></div>
    <div class="brand"><span class="brand__mark"></span>The Reed Kettle</div>

    <div class="person">
      <p class="person__name">Dana Whitlow</p>
      <p class="person__role">Managing Director</p>
    </div>

    <div class="divider"></div>

    <ul class="contacts">
      <li>
        <svg viewBox="0 0 10 10" aria-hidden="true"><path fill="#2e2923" d="M1 3.2 C1 2 2 1.3 5 1.3 C8 1.3 9 2 9 3.2 L7.4 3.8 L6.9 2.9 L3.1 2.9 L2.6 3.8 Z M2.3 4.6 L7.7 4.6 L8.6 8.8 L1.4 8.8 Z"/><circle cx="5" cy="6.6" r="1.1" fill="#c8a779"/></svg>
        +1 (555) 304-7712
      </li>
      <li>
        <svg viewBox="0 0 10 10" aria-hidden="true"><rect x="0.5" y="2" width="9" height="6.4" fill="#2e2923"/><path d="M0.8 2.4 L5 5.6 L9.2 2.4" fill="none" stroke="#c8a779" stroke-width="0.9"/></svg>
        reednkettle@mailbox.example
      </li>
      <li><span class="social-box"></span>facebook.com/reednkettle</li>
      <li><span class="social-box"></span>instagram.com/reednkettle</li>
    </ul>

    <p class="address">48206 Ludlow Row, #7,<br>Bexmoor Flats, Ca90000</p>

    <svg class="bands" viewBox="0 0 484 38" preserveAspectRatio="none" aria-hidden="true">
      <rect x="0" y="17" width="484" height="21" fill="var(--band-yellow)"/>
      <polygon points="270,0 484,0 484,38 254,38" fill="var(--band-orange)"/>
    </svg>
    <p class="website">www.reednkettle.example</p>
  </section>

</main>
</body>
</html>
```